Brintel Works - Fast, Efficient and Gas Mainteance for Domestic, Commercial and Industrial clients

We are in the process of purchasing a new business and would like to get a new logo and business card.
Business is a gas maintenance business that also does new gas installations.
Has been established since 1988.
Services include:
Install all types of gas appliances & equipment inc. hot water units
Maintain / repair / replace all types of gas appliances & equipment

Target Market(s)

Domestic, Commercial and Industrial clients

Industry/Entity Type

Business

Contact Information for Business Card

admin@brintelworks.com.au
07 3918 4726
Brintel Works PTY LTD

Logo Text

Gas Fitting & Plumbing Maintenance Specialists

Font styles to use
Sans Serif

Requirements
Must have
• Logo
• Business name, contact number, email address, web address
• Domestic | Commercial | Industrial Est Since 1988
Nice to have
• Possibly a black card with a flame logo to one side
Should not have
• Spelling errors

```html
<!DOCTYPE html>
<html lang="en">
<head>
<meta charset="utf-8">
<title>Brintel Works PTY LTD – Business Card</title>
<link href="https://fonts.googleapis.com/css2?family=Questrial&display=swap" rel="stylesheet">
<style>
  :root {
    --backdrop: #e4e3e1;
    --card-dark: #020202;
    --card-light: #ffffff;
    --brand-blue: #1a8fd3;
    --brand-blue-deep: #0f6fb4;
    --ink-grey: #4a4a4a;
    --ink-soft: #d9d9d9;
    --rule-grey: #b9b9b9;
  }
  * { box-sizing: border-box; margin: 0; padding: 0; }
  html, body { width: 1200px; height: 1189px; overflow: hidden; }
  body {
    background: var(--backdrop);
    font-family: "Questrial", "Helvetica Neue", Arial, sans-serif;
    position: relative;
  }
  .card {
    position: absolute;
    left: 220px;
    width: 760px;
    height: 465px;
    display: flex;
    flex-direction: column;
    align-items: center;
    box-shadow: 0 10px 30px rgba(0,0,0,0.18);
  }
  .card--back { top: 95px; background: var(--card-dark); color: var(--ink-soft); padding-top: 96px; }
  .card--front { top: 625px; background: var(--card-light); color: var(--ink-grey); padding-top: 70px; overflow: hidden; }

  .brand { display: flex; align-items: center; gap: 16px; }
  .brand__dot { width: 34px; height: 34px; border-radius: 50%; background: var(--brand-blue); }
  .brand__name { font-size: 38px; letter-spacing: 0.5px; }
  .card--back .brand__name { color: #e6e6e6; }
  .card--front .brand__name { color: var(--ink-grey); }
  .brand__since { font-size: 15px; margin-top: 6px; letter-spacing: 1px; }
  .card--back .brand__since { color: #cfcfcf; }
  .card--front .brand__since { color: #7a7a7a; }

  .services__title { font-size: 26px; margin-top: 40px; letter-spacing: 1px; color: #e0e0e0; }
  .services__list { margin-top: 28px; font-size: 21px; line-height: 1.5; text-align: center; color: #e0e0e0; }

  .contact__name { font-size: 34px; margin-top: 34px; color: var(--ink-grey); }
  .contact__line { font-size: 22px; margin-top: 10px; color: var(--ink-grey); }
  .contact__label { color: var(--brand-blue-deep); font-weight: 700; }

  .band {
    position: absolute; left: 0; right: 0; bottom: 0; height: 92px;
    background: linear-gradient(180deg, var(--brand-blue) 0%, var(--brand-blue-deep) 100%);
    display: flex; align-items: center; justify-content: center;
  }
  .band__web { color: #ffffff; font-size: 24px; letter-spacing: 0.5px; }
</style>
</head>
<body>
  <section class="card card--back" aria-label="Card back">
    <div class="brand">
      <span class="brand__dot"></span>
      <span class="brand__name">Brintel Works PTY LTD</span>
    </div>
    <p class="brand__since">since 1988</p>
    <h2 class="services__title">SERVICES</h2>
    <p class="services__list">
      Install all types of gas appliances &amp; equipment inc. hot water units<br>
      Maintain / repair / replace all types of gas appliances &amp; equipment
    </p>
  </section>

  <section class="card card--front" aria-label="Card front">
    <div class="brand">
      <span class="brand__dot"></span>
      <span class="brand__name">Brintel Works PTY LTD</span>
    </div>
    <p class="brand__since">since 1988</p>
    <p class="contact__name">Employee Name</p>
    <p class="contact__line"><span class="contact__label">Phone:</span> 07 3918 4726</p>
    <p class="contact__line"><span class="contact__label">Email:</span> admin@brintelworks.com.au</p>
    <div class="band">
      <span class="band__web">www.brintelworks.com.au</span>
    </div>
  </section>
</body>
</html>
```